Australian Trucking Company Requires Professional Looking Stationary

We require a professional looking stationary design that incorporates our newly designed logo.

Our business, called "Brell Haulage Contracting", provides contracting work, transport and logistics to business in Western Australia particularly with links to the mining sector.

We are a small business looking to expand and our new logo and our new stationary will help develop our brand image in our market place.

Target Market(s)

Businesses and Corporation with links to the Mining Sector

Industry/Entity Type

Small Business

Requirements
Must have
• The letterhead must have the following details:
The new logo

Text saying: "Brell Holdings Pty Ltd (ACN 582 316 907) ATF The Brell Discretionary Trust T/AS"
"ABN 71 834 209 553"
Address "P.O Box 817 Wattlegrove WA, 6958"
Phone: 08 9352 7140
Email: brellhaul@mailbox-example.com.au

The text on the letterhead should be editable as the details are likely to change in the near future. Provision should be made for a website address all though one isn't available at the moment.

The styling, layout and font text is entirely up to the designer.

```html
<!DOCTYPE html>
<html lang="en">
<head>
<meta charset="utf-8">
<title>Brell Haulage Contracting – Business Card</title>
<link rel="stylesheet" href="https://fonts.googleapis.com/css2?family=Open+Sans:wght@400;600;700;800&display=swap">
<style>
  :root {
    --backdrop: #e9e6e1;
    --card: #ffffff;
    --brand-red: #8e1117;
    --band-dark: #7a0a10;
    --band-light: #e0262c;
    --text-grey: #555555;
    --rule: #3a3a3a;
    --mark-grey: #6a6a6a;
  }
  * { box-sizing: border-box; margin: 0; padding: 0; }
  html, body {
    width: 1200px; height: 407px; overflow: hidden;
    background: var(--backdrop);
    font-family: "Open Sans", Arial, sans-serif;
  }
  .canvas { position: relative; width: 1200px; height: 407px; }
  .card {
    position: absolute; top: 60px; width: 504px; height: 288px;
    background: var(--card);
    box-shadow: 3px 4px 8px rgba(0,0,0,0.25);
    overflow: hidden;
  }
  .card--front { left: 58px; }
  .card--back { left: 638px; }

  .brand {
    position: absolute; top: 36px; left: 82px;
    display: flex; align-items: center; gap: 18px;
  }
  .brand__square { width: 80px; height: 80px; background: var(--mark-grey); }
  .brand__name {
    color: var(--brand-red); font-weight: 800;
    font-size: 27px; line-height: 28px; letter-spacing: 0.5px;
    text-transform: uppercase;
  }

  .entity {
    position: absolute; top: 131px; left: 0; width: 100%;
    text-align: center; font-size: 10.5px; color: var(--text-grey);
  }
  .person {
    position: absolute; top: 186px; left: 0; width: 100%;
    text-align: center; color: var(--brand-red);
  }
  .person__name { font-size: 16.5px; font-weight: 700; }
  .person__title { font-size: 12.5px; }
  .contact {
    position: absolute; left: 0; width: 100%;
    text-align: center; font-size: 10.5px; color: var(--text-grey);
  }
  .contact--lines { top: 215px; word-spacing: 1px; }
  .contact--lines span + span { margin-left: 8px; }
  .contact--post { top: 237px; }

  .rule {
    position: absolute; left: 0; top: 256px; width: 100%; height: 2px;
    background: var(--rule);
  }
  .band {
    position: absolute; left: 0; bottom: 0; width: 100%; height: 30px;
    background: linear-gradient(90deg, var(--band-dark) 0%, var(--band-light) 50%, var(--band-dark) 100%);
    display: flex; align-items: center; justify-content: center;
  }
  .band__web {
    color: #ffffff; font-weight: 700; font-size: 13.5px; letter-spacing: 2.6px;
  }
</style>
</head>
<body>
<div class="canvas">

  <section class="card card--front">
    <div class="brand">
      <div class="brand__square" aria-hidden="true"></div>
      <div class="brand__name">Brell<br>Haulage<br>Contracting</div>
    </div>
    <p class="entity">Brell Holdings Pty Ltd (ACN 582 316 907) ATF The Brell Discretionary Trust T/AS</p>
    <p class="person"><span class="person__name">Your Name</span><span class="person__title">, Title</span></p>
    <p class="contact contact--lines"><span>P: 08 9352 7140</span><span>E: brellhaul@mailbox-example.com.au</span><span>W: www.brellhaulage.com</span></p>
    <p class="contact contact--post">P.O Box 817 Wattlegrove WA, 6958</p>
    <div class="rule"></div>
    <div class="band"><span class="band__web">www.brellhaulage.com</span></div>
  </section>

  <section class="card card--back">
    <div class="brand">
      <div class="brand__square" aria-hidden="true"></div>
      <div class="brand__name">Brell<br>Haulage<br>Contracting</div>
    </div>
    <div class="rule"></div>
    <div class="band"><span class="band__web">www.brellhaulage.com</span></div>
  </section>

</div>
</body>
</html>
```